National Water and Fire Restoration, Multi Surface Cleaning, Carpet Cleaning Business Needs a Websi

We need a new fresh website for our business. There are multiple services we offer and we need a fresh corporate website that represents us better. We start from cleaning carpet and tiles, to upholstery and curtains, to completely clean all contents and building materials after a fire, or completely dry out a home or business after a major or minor flood event. We are open to all concepts as we want to create a new look, maybe even logo, signage, vehicle signage, uniforms.
We are open to new colours etc.

Go to www.brightvaleclean.com.au for current logo and all other past ideas

Reason: I need to see more quality designs to sink my teeth into

Target Market(s)

The target market is everyone of all walks of life

Industry/Entity Type

Business

Number of Pages Required

3 page

Font styles to use
Sans Serif

Requirements
Must have
• Home page
• Services page
• Contact us page
• The rest is up to your imagination
• ***This is design only - NO CODING REQUIRED***
Nice to have
• Pictures

```html
<!DOCTYPE html>
<html lang="en">
<head>
<meta charset="utf-8">
<title>Brightvale Clean Services</title>
<link href="https://fonts.googleapis.com/css2?family=Open+Sans:wght@400;600;700;800&family=Oswald:wght@500;600;700&display=swap" rel="stylesheet">
<style>
:root{
  --blue:#1b5aa6;
  --blue-dark:#0f3f7d;
  --navy:#16325c;
  --pink:#e2287c;
  --red:#d92b3a;
  --ink:#333;
  --muted:#777;
  --line:#e2e2e2;
  --soft:#f4f6f9;
  --footer:#2a2d31;
  --footer-2:#1f2125;
}
*{box-sizing:border-box;margin:0;padding:0}
html,body{width:1200px;height:2328px;overflow:hidden}
body{font-family:"Open Sans",Arial,sans-serif;color:var(--ink);background:#fff;font-size:13px;line-height:1.5}
.wrap{width:1120px;margin:0 auto;position:relative}
h2,h3,.hero-title{font-family:"Oswald",Arial,sans-serif}
a{color:inherit;text-decoration:none}

/* header */
.topbar{height:100px}
.topbar .wrap{display:flex;justify-content:space-between;align-items:center;height:100px}
.brand{display:flex;align-items:center;gap:12px}
.brand-dot{width:46px;height:46px;border-radius:50%;background:var(--blue)}
.brand-name{font-weight:800;font-size:26px;color:var(--blue);line-height:1}
.top-right{text-align:right}
.top-contact{display:flex;gap:14px;justify-content:flex-end;align-items:center}
.phone{font-size:22px;font-weight:700;color:var(--blue)}
.email{border:1px solid var(--line);padding:4px 10px;font-size:12px;color:var(--muted);border-radius:3px}
.tagline{margin-top:8px;font-weight:800;font-size:17px;color:var(--pink)}
.tagline span{color:var(--blue)}

.nav{height:38px;background:linear-gradient(#2468b8,var(--blue-dark))}
.nav ul{list-style:none;display:flex;height:38px;align-items:center}
.nav li{color:#fff;font-weight:700;font-size:13px;padding:0 22px;border-right:1px solid rgba(255,255,255,.2);height:38px;display:flex;align-items:center}
.nav li.home{padding:0 18px;background:var(--pink)}

/* hero */
.hero{height:400px;background:linear-gradient(90deg,#eef3f8 0,#f7f9fb 40%,#d9c3a8 60%,#c9a987 100%);position:relative;overflow:hidden}
.hero-photo{position:absolute;right:0;top:0;width:720px;height:400px;background:linear-gradient(120deg,#e9dccb,#c8a782 55%,#a07d5d)}
.hero-copy{position:relative;z-index:1;padding:40px 0 0 40px;width:440px}
.hero-title{color:var(--red);font-size:40px;font-weight:700;line-height:1.1}
.hero-list{list-style:none;margin:20px 0 22px}
.hero-list li{font-weight:800;font-size:20px;color:var(--navy);display:flex;align-items:center;gap:10px;margin-bottom:6px}
.hero-list li::before{content:"";width:12px;height:12px;background:var(--pink)}
.offer{font-weight:800;font-size:19px;color:var(--blue);line-height:1.3}
.offer em{font-style:normal;color:var(--red)}
.btn-signup{display:inline-block;margin-top:22px;background:var(--pink);color:#fff;font-weight:800;font-size:18px;padding:10px 24px;border-radius:3px}

/* welcome */
.welcome{text-align:center;padding:38px 0 0;height:380px}
.welcome h2{font-size:30px;font-weight:600;color:var(--navy)}
.welcome h2 b{color:var(--blue)}
.welcome .sub{font-weight:700;font-size:15px;margin-top:6px;color:var(--navy)}
.welcome .sub span{background:var(--pink);color:#fff;padding:1px 6px}
.welcome p{text-align:left;margin:22px 60px 0;font-size:13px;color:#555}
.welcome p b{color:var(--red)}
.btn{display:inline-block;margin-top:22px;background:var(--blue);color:#fff;font-size:12px;font-weight:700;padding:7px 18px;border-radius:2px}

/* services */
.section-title{text-align:center;font-size:30px;font-weight:600;color:var(--navy);position:relative}
.section-title b{color:var(--pink)}
.section-title::before,.section-title::after{content:"";position:absolute;top:50%;width:360px;height:1px;background:var(--line)}
.section-title::before{left:40px}.section-title::after{right:40px}
.services{height:420px}
.cards{display:flex;gap:28px;margin-top:26px}
.card{flex:1;background:#fff;border:1px solid var(--line)}
.card h3{background:var(--pink);color:#fff;font-size:16px;font-weight:500;text-align:center;padding:8px 0;letter-spacing:.5px}
.card-img{height:130px;margin:12px 12px 0}
.card p{padding:12px 14px 6px;font-size:12px;color:#666}
.card .more{padding:0 14px 14px;font-weight:700;font-size:12px;color:var(--blue)}

/* triple */
.triple{display:flex;gap:30px;height:300px;padding-top:20px}
.col{flex:1}
.col h3{font-size:26px;font-weight:600;color:var(--navy);margin-bottom:14px}
.col h3 b{color:var(--pink)}
.sched{height:190px;background:linear-gradient(135deg,#2a78c8,#12427f);position:relative}
.sched-cta{position:absolute;left:14px;bottom:16px;right:14px;color:#fff;font-weight:800;font-size:17px;line-height:1.25}
.sched-cta span{display:inline-block;margin-top:8px;background:var(--red);padding:3px 10px;font-size:16px}
.water-img{height:140px;background:linear-gradient(135deg,#f29a3e,#c8431d)}
.water-list{display:grid;grid-template-columns:1fr 1fr;gap:6px 10px;margin-top:12px;font-size:12px;color:#555}
.water-list li,.why li{list-style:none;display:flex;align-items:center;gap:8px}
.water-list li::before{content:"";width:8px;height:8px;background:var(--blue);border-radius:50%}
.why li{border-bottom:1px solid var(--line);padding:7px 0;font-size:12.5px;font-weight:600;color:#444}
.why svg{flex:none}

/* testimonials */
.testi{height:290px;padding-top:14px}
.testi h3{font-size:28px;font-weight:600;color:var(--navy);border-bottom:1px solid var(--line);padding-bottom:8px}
.testi h3 b{color:var(--pink)}
.testi-body{display:flex;gap:30px;margin-top:20px;align-items:flex-start}
.person{width:140px;height:140px;background:linear-gradient(#b8c7d8,#7d90a6)}
.quote{flex:1;font-size:13px;color:#555;font-style:italic}
.quote b{display:block;margin-top:14px;font-style:normal;color:var(--red);font-size:14px}
.dots{display:flex;gap:6px;margin-top:16px;justify-content:center}
.dots i{width:9px;height:9px;border-radius:50%;background:#ccc}
.dots i:first-child{background:var(--blue)}
.seal{width:170px;height:170px;border-radius:50%;background:#c7202f;flex:none}

/* partners */
.partners{height:190px;padding-top:10px}
.partners h3{font-size:28px;font-weight:600;color:var(--navy);border-bottom:1px solid var(--line);padding-bottom:8px}
.partners h3 b{color:var(--pink)}
.partner-row{display:flex;justify-content:space-between;align-items:center;margin-top:34px;padding:0 20px}
.partner{font-weight:800;font-size:26px;color:#3a3a3a}

/* footer */
.footer{background:var(--footer);color:#bbb;height:210px;padding-top:26px}
.footer .wrap{display:flex;gap:40px}
.fcol h4{color:#fff;font-size:15px;font-weight:700;margin-bottom:12px}
.fcol ul{list-style:none;font-size:12px;line-height:1.9}
.links{display:grid;grid-template-columns:110px 130px}
.fcol.contact{width:260px;font-size:12px;line-height:1.8}
.fcol.news{flex:1;font-size:12px}
.sub-form{display:flex;margin-top:12px}
.sub-form span{flex:1;background:#fff;color:#999;padding:6px 10px}
.sub-form b{background:var(--blue);color:#fff;padding:6px 14px}
.badge{width:150px;height:60px;background:#4a9a3c;border-radius:4px;margin-top:34px}
.copy{position:absolute;left:0;right:0;bottom:0;height:28px;background:var(--footer-2);color:#888;font-size:11px;text-align:right;padding:6px 40px}
.footer{position:relative}
</style>
</head>
<body>

<header class="topbar">
  <div class="wrap">
    <div class="brand"><span class="brand-dot"></span><span class="brand-name">Brightvale Clean</span></div>
    <div class="top-right">
      <div class="top-contact">
        <span class="phone">07 5550 1842</span>
        <span class="email">hello@brightvaleclean.com.au</span>
      </div>
      <div class="tagline">CLEAN - REFRESHED - <span>SAFE for YOU!</span></div>
    </div>
  </div>
</header>

<nav class="nav">
  <div class="wrap">
    <ul>
      <li class="home"><svg width="16" height="14" viewBox="0 0 16 14"><path d="M8 0 0 7h2v7h4V9h4v5h4V7h2z" fill="#fff"/></svg></li>
      <li>ABOUT US</li><li>SERVICES</li><li>COMMERCIAL</li><li>SCHEDULE &amp; JOB</li><li>MATERIAL PROGRAM</li><li>CONTACT US</li><li>LINKS</li>
    </ul>
  </div>
</nav>

<section class="hero">
  <div class="hero-photo" role="img" aria-label="Smiling family relaxing together on a clean sofa"></div>
  <div class="hero-copy">
    <div class="hero-title">PROFESSIONAL CLEANERS</div>
    <ul class="hero-list"><li>CARPETS</li><li>RUGS</li><li>FLOORS AND FINE FABRICS</li></ul>
    <div class="offer">OUR NEW EXCLUSIVE INTERNET<br>OFFERS AND <em>SAVE $$$</em></div>
    <a class="btn-signup">SIGN UP NOW</a>
  </div>
</section>

<section class="welcome">
  <div class="wrap">
    <h2>Welcome To <b>BRIGHTVALE</b></h2>
    <div class="sub">TO PROVIDE YOU WITH THE MOST OUTSTANDING SERVICE EXPERIENCE <span>EVER!</span></div>
    <p><b>Brightvale Clean Services</b> is a professional, full-service carpet, floor, fabric care company serving the coastal regions and nearby towns. Brightvale has been in business since 1996. At Brightvale Clean Services, we take pride in our reputation, experience, education, systems and guarantees. Our technicians are fully certified and hold the industry's most recognised body of qualifications for carpet and upholstery cleaning, flood drying and fire restoration work across homes and businesses.</p>
    <a class="btn">Read More »</a>
  </div>
</section>

<section class="services">
  <div class="wrap">
    <h2 class="section-title">Our <b>Services</b></h2>
    <div class="cards">
      <div class="card"><h3>CARPET CLEANING</h3><div class="card-img" role="img" aria-label="Technician cleaning a carpet" style="background:linear-gradient(135deg,#b9c9d9,#6f8aa6)"></div><p>Deep steam cleaning lifts dirt, stains and allergens from every fibre, leaving carpets fresh and dry fast.</p><div class="more">Read More »</div></div>
      <div class="card"><h3>UPHOLSTERY CLEANING</h3><div class="card-img" role="img" aria-label="Upholstered sofa being cleaned" style="background:linear-gradient(135deg,#d8c6b0,#9c8062)"></div><p>Gentle methods for sofas, chairs and fine fabrics restore colour and comfort without harsh residue.</p><div class="more">Read More »</div></div>
      <div class="card"><h3>LEATHER CLEANING</h3><div class="card-img" role="img" aria-label="Leather lounge suite" style="background:linear-gradient(135deg,#a87a56,#5e3d26)"></div><p>Careful cleaning and conditioning protects leather furniture and keeps it soft, supple and lasting.</p><div class="more">Read More »</div></div>
      <div class="card"><h3>RUG CLEANING</h3><div class="card-img" role="img" aria-label="Patterned rug on a floor" style="background:linear-gradient(135deg,#c9a1a0,#7e4c4f)"></div><p>Specialist care for wool, silk and synthetic rugs brings back bright colours and a soft clean pile.</p><div class="more">Read More »</div></div>
    </div>
  </div>
</section>

<section class="wrap triple">
  <div class="col">
    <h3>Cleaning <b>Schedule</b></h3>
    <div class="sched" role="img" aria-label="Company service van">
      <div class="sched-cta">CLICK HERE TO SCHEDULE<br>YOUR CLEANING TODAY.<br><span>SAVE 20%</span></div>
    </div>
  </div>
  <div class="col">
    <h3>Water <b>Damage</b></h3>
    <div class="water-img" role="img" aria-label="Flood drying equipment and emergency hotline banner"></div>
    <ul class="water-list"><li>Quick Dry Out</li><li>Mould Control</li><li>Odour Removal</li><li>24 Hour Callout</li></ul>
  </div>
  <div class="col why">
    <h3>Why <b>Choose Us</b></h3>
    <ul>
      <li><svg width="16" height="16"><circle cx="8" cy="8" r="8" fill="#1b5aa6"/><path d="M4 8l3 3 5-6" stroke="#fff" stroke-width="2" fill="none"/></svg>Reputation</li>
      <li><svg width="16" height="16"><circle cx="8" cy="8" r="8" fill="#1b5aa6"/><path d="M4 8l3 3 5-6" stroke="#fff" stroke-width="2" fill="none"/></svg>Experience</li>
      <li><svg width="16" height="16"><circle cx="8" cy="8" r="8" fill="#1b5aa6"/><path d="M4 8l3 3 5-6" stroke="#fff" stroke-width="2" fill="none"/></svg>Education &amp; Certification</li>
      <li><svg width="16" height="16"><circle cx="8" cy="8" r="8" fill="#1b5aa6"/><path d="M4 8l3 3 5-6" stroke="#fff" stroke-width="2" fill="none"/></svg>Cleaning Systems</li>
      <li><svg width="16" height="16"><circle cx="8" cy="8" r="8" fill="#1b5aa6"/><path d="M4 8l3 3 5-6" stroke="#fff" stroke-width="2" fill="none"/></svg>First Class Customer Service</li>
      <li><svg width="16" height="16"><circle cx="8" cy="8" r="8" fill="#1b5aa6"/><path d="M4 8l3 3 5-6" stroke="#fff" stroke-width="2" fill="none"/></svg>100% Money Back Guarantee</li>
    </ul>
  </div>
</section>

<section class="wrap testi">
  <h3>Client <b>Testimonials</b></h3>
  <div class="testi-body">
    <div class="person" role="img" aria-label="Portrait of a satisfied client"></div>
    <div class="quote">
      “The team arrived right on time, explained every step and left our carpets looking brand new. After a burst pipe flooded our lounge they had the whole room dried out within days. Friendly, careful and honest people. We would recommend Brightvale to anyone needing a reliable cleaning service.”
      <b>Mr. Daniel Hart</b>
      <div class="dots"><i></i><i></i><i></i><i></i></div>
    </div>
    <div class="seal" role="img" aria-label="Years of service anniversary badge"></div>
  </div>
</section>

<section class="wrap partners">
  <h3>Our <b>Partner</b></h3>
  <div class="partner-row">
    <span class="partner">Northline</span>
    <span class="partner">Kestro</span>
    <span class="partner">Fluxa</span>
    <span class="partner">Aerivo</span>
    <span class="partner">Greenloop</span>
  </div>
</section>

<footer class="footer">
  <div class="wrap">
    <div class="fcol">
      <h4>Quick Links</h4>
      <ul class="links"><li>› Home</li><li>› Schedule &amp; Job</li><li>› About Us</li><li>› Referral Program</li><li>› Services</li><li>› Contact Us</li><li>› Commercial</li><li>› Links</li></ul>
    </div>
    <div class="fcol contact">
      <h4>Contact Details</h4>
      14 Harbour Rd, Portvale QLD 4870<br>Phone: 07 5550 1842<br>Trading as Brightvale Clean Services<br>PO Box 210, Portvale QLD 4870<br>Office: 07 5550 1843
    </div>
    <div class="fcol news">
      <h4>Newsletter</h4>
      Subscribe to our newsletter to receive our special offers and news.
      <div class="sub-form"><span>Email Address</span><b>Subscribe</b></div>
    </div>
    <div class="badge" role="img" aria-label="Industry membership badge"></div>
  </div>
  <div class="copy">Copyright © 2014 Brightvale Clean</div>
</footer>

</body>
</html>
```